Oil and Gas Exploration and Production company needs a business card design

We need a business card design using our logo and colors in the logo. We want a mainstream design.

```html
<!DOCTYPE html>
<html lang="en">
<head>
<meta charset="utf-8">
<title>Solara Energy – Business Card</title>
<link href="https://fonts.googleapis.com/css2?family=Arvo:wght@400;700&family=Roboto:wght@400&display=swap" rel="stylesheet">
<style>
  :root {
    --backdrop: #e4e0da;
    --paper: #f4f4f2;
    --gold: #c8982e;
    --ink: #1f1b1c;
    --text: #3a3a3a;
    --white: #ffffff;
  }
  * { box-sizing: border-box; margin: 0; padding: 0; }
  html, body {
    width: 1200px; height: 960px; overflow: hidden;
    background: var(--backdrop);
  }
  .canvas { position: relative; width: 1200px; height: 960px; }
  .card {
    position: absolute; width: 600px; height: 342px; overflow: hidden;
    box-shadow: 0 3px 6px rgba(0,0,0,0.25);
  }
  .card--front { left: 314px; top: 113px; background: var(--paper); }
  .card--back { left: 311px; top: 472px; background: var(--gold); }

  .front-panel {
    position: absolute; inset: 0; background: var(--gold);
    clip-path: polygon(78% 0, 100% 0, 100% 100%, 56% 100%);
  }

  .brand { position: absolute; display: flex; align-items: center; gap: 10px; }
  .brand__dot { width: 22px; height: 22px; border-radius: 50%; background: var(--gold); flex: none; }
  .brand__name {
    font-family: "Arvo", serif; font-weight: 700; color: var(--ink);
    white-space: nowrap; letter-spacing: -0.5px;
  }
  .card--front .brand { left: 41px; top: 60px; }
  .card--front .brand__name { font-size: 40px; }
  .card--back .brand { left: 0; right: 0; top: 140px; justify-content: center; }
  .card--back .brand__dot { background: var(--ink); width: 26px; height: 26px; }
  .card--back .brand__name { font-size: 50px; }

  .contact { position: absolute; left: 40px; top: 170px; font-family: "Arvo", serif; }
  .contact__name { font-size: 20px; font-weight: 700; color: var(--ink); letter-spacing: 1px; }
  .contact__role { font-size: 14px; color: var(--gold); margin-top: 3px; }
  .contact__address { font-size: 13px; color: var(--text); line-height: 19px; margin-top: 14px; }
  .contact__lines { font-size: 13px; color: var(--text); line-height: 19px; margin-top: 9px; }
  .contact__label { color: var(--ink); font-weight: 400; }

  .web {
    position: absolute; left: 0; right: 0; top: 287px; text-align: center;
    font-family: "Roboto", sans-serif; font-size: 14px; letter-spacing: 4px; color: var(--white);
  }
</style>
</head>
<body>
<main class="canvas">
  <section class="card card--front" aria-label="Business card front">
    <div class="front-panel"></div>
    <div class="brand">
      <span class="brand__dot"></span>
      <span class="brand__name">Solara Energy</span>
    </div>
    <div class="contact">
      <p class="contact__name">DANIEL REYES</p>
      <p class="contact__role">CEO/FOUNDER</p>
      <p class="contact__address">2140 Birchwood Road<br>Fairbanks, Alaska 99701</p>
      <p class="contact__lines">
        <span class="contact__label">PHONE:</span> 555 210 4870<br>
        <span class="contact__label">EMAIL:</span> info@solaraenergy.com
      </p>
    </div>
  </section>

  <section class="card card--back" aria-label="Business card back">
    <div class="brand">
      <span class="brand__dot"></span>
      <span class="brand__name">Solara Energy</span>
    </div>
    <p class="web">www.solaraenergy.com</p>
  </section>
</main>
</body>
</html>
```